All-Natural Head Lice Removal company

I need a business card with my pre-existing logo. We are a new company located in Portland Oregon that goes into peoples homes to help with head lice removal. My products and approach are all- natural and also will be around children.On my current logo we used Teal Bl and the color Green. I am open to new ideas just want it simple and creative

Target Market(s)

my biggest market is families of school aged children

Industry/Entity Type

Business

Contact Information for Business Card

see upload for details from previous business card

Font styles to use
Serif

Colors
33a6d7
9bcb3b
f37122

Requirements
Must have
• Basic information/ logo put into a creative format that is catching to the eye
Nice to have
• creative

```html
<!DOCTYPE html>
<html lang="en">
<head>
<meta charset="utf-8">
<title>Nitpick – Business Card</title>
<link href="https://fonts.googleapis.com/css2?family=Arvo:wght@400;700&display=swap" rel="stylesheet">
<style>
  :root {
    --teal-blue: #33a6d7;
    --sky-blue: #8fd3f0;
    --leaf-green: #9bcb3b;
    --ink: #1b1b1b;
    --charcoal: #2a2a2a;
    --paper: #ffffff;
    --backdrop: #ece8e2;
  }
  * { margin: 0; padding: 0; box-sizing: border-box; }
  html, body { width: 1200px; height: 913px; overflow: hidden; }
  body {
    background: var(--backdrop);
    font-family: "Arvo", Georgia, serif;
    position: relative;
  }
  .card {
    position: absolute;
    top: 302px;
    width: 540px;
    height: 309px;
    border-radius: 18px;
    overflow: hidden;
    box-shadow: 0 10px 28px rgba(0,0,0,0.18);
  }
  .card-front { left: 40px; }
  .card-back { left: 620px; background: var(--paper); }
  .card-shapes { position: absolute; inset: 0; }

  .brand { position: absolute; display: flex; align-items: center; gap: 10px; }
  .brand-dot { width: 46px; height: 46px; border-radius: 50%; background: var(--leaf-green); }
  .brand-name { font-weight: 700; font-size: 30px; color: var(--ink); }

  .card-front .brand { left: 30px; top: 118px; }
  .front-tagline {
    position: absolute; right: 24px; top: 34px;
    color: var(--paper); font-size: 14px;
  }
  .holder { position: absolute; right: 24px; top: 92px; text-align: right; color: var(--paper); }
  .holder-name { font-size: 20px; letter-spacing: 1px; }
  .holder-rule { height: 1px; background: var(--paper); width: 300px; margin: 3px 0 2px auto; }
  .holder-title { font-size: 10px; letter-spacing: 1px; color: var(--ink); }
  .front-divider { position: absolute; left: 30px; right: 200px; top: 186px; height: 1px; background: var(--paper); opacity: 0.85; }
  .contact-list { position: absolute; left: 30px; top: 196px; list-style: none; color: var(--paper); font-size: 13px; line-height: 19px; }
  .contact-list li { display: flex; align-items: center; gap: 8px; }
  .contact-list svg { width: 11px; height: 11px; fill: var(--paper); }

  .card-back .brand { right: 40px; top: 48px; }
  .back-taglines { position: absolute; left: 30px; top: 188px; font-weight: 700; font-size: 14.5px; line-height: 20px; color: var(--ink); }
  .back-url { position: absolute; left: 28px; bottom: 16px; color: var(--paper); font-size: 13px; }
</style>
</head>
<body>

<section class="card card-front">
  <svg class="card-shapes" viewBox="0 0 540 309" aria-hidden="true">
    <defs>
      <linearGradient id="frontSky" x1="0" y1="0" x2="0" y2="1">
        <stop offset="0" stop-color="#8fd3f0"/>
        <stop offset="1" stop-color="#33a6d7"/>
      </linearGradient>
    </defs>
    <rect width="540" height="309" fill="url(#frontSky)"/>
    <rect x="0" y="268" width="400" height="41" fill="#1b1b1b"/>
    <path d="M372,309 C372,252 392,222 440,222 L540,222 L540,309 Z" fill="#ffffff"/>
  </svg>
  <div class="brand"><span class="brand-dot"></span><span class="brand-name">Nitpick</span></div>
  <p class="front-tagline">All Natural In-Home Lice Removal Services</p>
  <div class="holder">
    <p class="holder-name">MAREN ELLISON</p>
    <div class="holder-rule"></div>
    <p class="holder-title">OWNER</p>
  </div>
  <div class="front-divider"></div>
  <ul class="contact-list">
    <li><svg viewBox="0 0 12 12"><path d="M2.5 0.5 L4.5 0.5 L5.3 3.2 L4 4.3 C4.7 5.9 6 7.2 7.7 8 L8.8 6.7 L11.5 7.5 L11.5 9.5 C11.5 10.6 10.6 11.5 9.5 11.5 C4.5 11.5 0.5 7.5 0.5 2.5 C0.5 1.4 1.4 0.5 2.5 0.5Z"/></svg>1-855-555-NITS (6487)</li>
    <li><svg viewBox="0 0 12 12"><path d="M0.5 2 H11.5 V10 H0.5 Z M1.5 3 V3.4 L6 6.6 L10.5 3.4 V3 Z" fill-rule="evenodd"/></svg>maren@nitpickhome.com</li>
    <li><svg viewBox="0 0 12 12"><circle cx="6" cy="6" r="5.5"/></svg>www.nitpickhome.com</li>
  </ul>
</section>

<section class="card card-back">
  <svg class="card-shapes" viewBox="0 0 540 309" aria-hidden="true">
    <path d="M250,309 L250,252 C250,242 258,238 270,238 L540,238 L540,309 Z" fill="#33a6d7"/>
    <path d="M0,309 L0,264 L222,264 C248,264 256,246 264,238 L300,238 L300,244 C284,250 276,309 276,309 Z" fill="#1b1b1b"/>
  </svg>
  <div class="brand"><span class="brand-dot"></span><span class="brand-name">Nitpick</span></div>
  <p class="back-taglines">Try Nitpick Today and Be Lice Free Tomorrow!<br>All Natural In-Home Lice Removal Services</p>
  <p class="back-url">www.nitpickhome.com</p>
</section>

</body>
</html>
```